Business Card Design for ReaL ESTATE AGENT

New Business Cards for a real estate agent in Jacksonville, FL. My specialty is urban core, historic districts but sell through out the city. Company Name is Ninth and Crest Realty a division of the Dunholt Companies. The card needs to convey an essence of professionalism, knowledge and success.

Target Market(s)

Home buyers and Sellers

Industry/Entity Type

Real Estate

Contact Information for Business Card

Double sided

Font styles to use
Sans Serif

Requirements
Must have
• My logs and photo (provided). My contact information as follows:
• Owen Talbrick
• Cell 904-555-0183
• Office 904-555-0147
• Email owentalbrick@mailbrook.example
Nice to have
• Tag Line - Exceptional Effort. Proven Results.

```html
<!DOCTYPE html>
<html lang="en">
<head>
<meta charset="utf-8">
<title>Ninth &amp; Crest Realty – Business Card</title>
<link rel="stylesheet" href="https://fonts.googleapis.com/css2?family=Lato:wght@400;700&display=swap">
<style>
  :root {
    --bg-top: #2a2a2a;
    --bg-bottom: #050505;
    --card: #ffffff;
    --accent: #e8492f;
    --ink: #2b2b2b;
    --photo-dark: #1e3138;
    --photo-mid: #3f5a60;
  }
  * { margin: 0; padding: 0; box-sizing: border-box; }
  html, body { width: 1200px; height: 900px; overflow: hidden; }
  body {
    position: relative;
    background: linear-gradient(180deg, var(--bg-top) 0%, var(--bg-bottom) 100%);
    font-family: "Lato", sans-serif;
    color: var(--ink);
  }
  .card {
    position: absolute;
    top: 184px;
    height: 490px;
    background: var(--card);
    border-radius: 12px;
  }
  .card--front { left: 299px; width: 301px; }
  .card--back { left: 645px; width: 305px; display: flex; align-items: center; justify-content: center; }

  .portrait {
    position: absolute;
    left: 60px;
    top: 44px;
    width: 175px;
    height: 203px;
    border-radius: 6px;
    background: radial-gradient(ellipse at 50% 45%, var(--photo-mid) 0%, var(--photo-dark) 75%);
  }
  .agent-name {
    position: absolute;
    top: 304px;
    width: 100%;
    text-align: center;
    font-size: 23px;
    font-weight: 400;
    color: var(--accent);
    letter-spacing: 0.3px;
    line-height: 28px;
  }
  .agent-title {
    position: absolute;
    top: 333px;
    width: 100%;
    text-align: center;
    font-size: 14px;
    line-height: 18px;
  }
  .contact {
    position: absolute;
    top: 369px;
    width: 100%;
    list-style: none;
    font-size: 14px;
    line-height: 20px;
  }
  .contact li { display: flex; align-items: center; justify-content: center; gap: 7px; }
  .contact svg { width: 10px; height: 10px; flex: none; }
  .contact .icon-fill { fill: var(--accent); }
  .contact .icon-line { fill: none; stroke: var(--card); stroke-width: 0.9; }

  .brand {
    display: flex;
    align-items: center;
    gap: 10px;
    color: var(--accent);
    font-weight: 700;
    font-size: 24px;
    letter-spacing: 0.5px;
    line-height: 30px;
  }
  .brand-dot { width: 14px; height: 14px; border-radius: 50%; background: var(--accent); flex: none; }
</style>
</head>
<body>
  <section class="card card--front">
    <div class="portrait" role="img" aria-label="Portrait photo of the agent"></div>
    <h1 class="agent-name">OWEN TALBRICK</h1>
    <p class="agent-title">Managing Director</p>
    <ul class="contact">
      <li>
        <svg viewBox="0 0 10 10" aria-hidden="true"><path class="icon-fill" d="M1 3.5C1 2 2.5 1 5 1s4 1 4 2.5L7.5 4 7 3H3L2.5 4zM2.5 5h5l1 4h-7z"/></svg>
        <span>Cell 904-555-0183</span>
      </li>
      <li>
        <svg viewBox="0 0 10 10" aria-hidden="true"><path class="icon-fill" d="M1 3.5C1 2 2.5 1 5 1s4 1 4 2.5L7.5 4 7 3H3L2.5 4zM2.5 5h5l1 4h-7z"/></svg>
        <span>Office 904-555-0147</span>
      </li>
      <li>
        <svg viewBox="0 0 10 10" aria-hidden="true"><rect class="icon-fill" x="0.5" y="2" width="9" height="6"/><path class="icon-line" d="M0.8 2.4L5 5.4l4.2-3"/></svg>
        <span>owentalbrick@mailbrook.example</span>
      </li>
    </ul>
  </section>

  <section class="card card--back">
    <div class="brand">
      <span class="brand-dot" aria-hidden="true"></span>
      <span class="brand-name">Ninth &amp; Crest Realty</span>
    </div>
  </section>
</body>
</html>
```